Business Card Design - Service Company

Use of the card mainly in living rooms and relations b2b We wish a card with a modern design, blue tones in the background would be a plus The card must be front / back (one side with the logo / the other with the information of contact )

Font styles to use
Serif

Requirements
Must have
• Using the map on the back of the business card Editable format! Photoshop CS2 / Illustrator CS2
Nice to have
• Mivrel Data IT Plein Ouest Commercial Center, 20417 Valcorbe 0491847352 Siret 41873306200018 APE 4793K https://www.fb.com/boutiquetech.mivreldata www.mivrel-data.com

```html
<!DOCTYPE html>
<html lang="en">
<head>
<meta charset="utf-8">
<title>Mivrel Data IT – Business Card</title>
<link rel="stylesheet" href="https://fonts.googleapis.com/css2?family=Lora:wght@400;700&display=swap">
<style>
  :root {
    --brand-blue: #2589cc;
    --ink-grey: #5b5b5b;
    --card-white: #ffffff;
    --rule-grey: #c9c9c9;
    --stage: #2b2b2b;
  }
  * { box-sizing: border-box; margin: 0; padding: 0; }
  html, body { width: 1200px; height: 880px; overflow: hidden; }
  body {
    background: var(--stage);
    font-family: "Lora", Georgia, serif;
    position: relative;
  }
  .card {
    position: absolute;
    width: 640px;
    height: 366px;
    border-radius: 22px;
    overflow: hidden;
    box-shadow: 0 10px 30px rgba(0,0,0,.45);
  }
  .card--front { left: 80px; top: 60px; background: var(--brand-blue); }
  .card--back { left: 480px; top: 454px; background: var(--card-white); }

  .wordmark {
    display: flex;
    align-items: center;
    gap: 12px;
    font-weight: 700;
    font-size: 40px;
    letter-spacing: 1px;
    text-transform: uppercase;
    white-space: nowrap;
  }
  .wordmark__square { width: 16px; height: 16px; flex: none; }
  .card--front .wordmark {
    position: absolute; left: 50%; top: 50%;
    transform: translate(-50%, -50%);
    color: var(--card-white);
  }
  .card--front .wordmark__square { background: var(--card-white); }

  .card--back .wordmark {
    position: absolute; left: 34px; top: 128px;
    font-size: 27px;
    color: var(--brand-blue);
  }
  .card--back .wordmark__square { background: var(--ink-grey); width: 12px; height: 12px; }

  .divider {
    position: absolute; left: 300px; top: 40px;
    width: 1.5px; height: 180px;
    background: var(--brand-blue);
  }
  .contact {
    position: absolute; left: 322px; top: 42px;
    color: var(--ink-grey);
    font-size: 14px;
    line-height: 1.35;
  }
  .contact__company {
    color: var(--brand-blue);
    font-weight: 700;
    text-transform: uppercase;
    font-size: 15px;
    margin-bottom: 2px;
  }
  .contact__list { list-style: none; margin-top: 12px; }
  .contact__item { display: flex; align-items: center; gap: 8px; font-size: 13.5px; }
  .contact__icon {
    width: 16px; height: 16px; flex: none;
    border-radius: 50%;
    background: var(--ink-grey);
    display: flex; align-items: center; justify-content: center;
  }
  .legal-band {
    position: absolute; left: 0; right: 0; bottom: 34px;
    height: 58px;
    background: var(--brand-blue);
    border-top: 4px solid var(--rule-grey);
    display: flex; align-items: center; justify-content: center;
    color: var(--card-white);
    font-size: 15px;
  }
  .legal-band::after {
    content: ""; position: absolute; left: 0; right: 0; bottom: -12px;
    height: 6px; background: var(--rule-grey);
  }
</style>
</head>
<body>
  <section class="card card--front" aria-label="Card front">
    <div class="wordmark"><span class="wordmark__square"></span>Mivrel Data IT</div>
  </section>

  <section class="card card--back" aria-label="Card back">
    <div class="wordmark"><span class="wordmark__square"></span>Mivrel Data IT</div>
    <div class="divider"></div>
    <div class="contact">
      <p class="contact__company">Mivrel Data IT</p>
      <p>Plein Ouest Commercial Center</p>
      <p>20417 Valcorbe</p>
      <ul class="contact__list">
        <li class="contact__item">
          <span class="contact__icon">
            <svg width="10" height="10" viewBox="0 0 10 10"><path d="M2 1l2 2-1 1c.6 1.3 1.7 2.4 3 3l1-1 2 2-1.3 1.2C4.5 9 1 5.5 .8 2.3z" fill="#fff"/></svg>
          </span>0491847352
        </li>
        <li class="contact__item"><span class="contact__icon"></span>boutiquetech.mivreldata</li>
        <li class="contact__item">
          <span class="contact__icon">
            <svg width="12" height="12" viewBox="0 0 12 12" fill="none" stroke="#fff" stroke-width="1"><circle cx="6" cy="6" r="4.5"/><ellipse cx="6" cy="6" rx="2" ry="4.5"/><path d="M1.5 6h9"/></svg>
          </span>www.mivrel-data.com
        </li>
      </ul>
    </div>
    <div class="legal-band">Siret 41873306200018 APE 4793K</div>
  </section>
</body>
</html>
```